Business Card for a Jewellery Brand

Business card for an upscale jewellery brand. Attached is the brand logo and icon and color board. I am looking for two card versions: one for the founder and one is generic. The card should be elegant and convey upscale and premium feel. I am open to both square and rectangle card shapes.

Industry/Entity Type

Jewelry

Contact Information for Business Card

Two cards: (1) Sunela Parvaniya (Founder) (2) General
(1) Sunela Parvaniya card should have Name: Sunela Parvaniya, Title: Founder Email id: sunela@quiremo.com.au. Phone no: +61452913307
(2) Generic card should have Email id: info@quiremo.com.au. Phone no: +61436207518

Requirements
Must have
• Workmark
• ICON
• Phone no
• Email ID
• ABN: 58219740312 (Note: ABN is Business number in Australia)
• Website: www.quiremo.com.au
• Instagram: quiremo_jewellery
• Facebook: @quiremojewellery
Nice to have
• Tagline

```html
<!DOCTYPE html>
<html lang="en">
<head>
<meta charset="UTF-8">
<title>Quiremo Business Cards</title>
<link href="https://fonts.googleapis.com/css2?family=Open+Sans:wght@400;600&display=swap" rel="stylesheet">
<style>
  :root {
    --canvas: #3a3230;
    --card: #1f1f1f;
    --rose: #e39a92;
    --white: #f4f4f4;
    --text-font: "Open Sans", Arial, sans-serif;
  }
  * { margin: 0; padding: 0; box-sizing: border-box; }
  html, body {
    width: 1200px;
    height: 844px;
    overflow: hidden;
    background: var(--canvas);
    font-family: var(--text-font);
  }
  .canvas {
    position: relative;
    width: 1200px;
    height: 844px;
    display: flex;
    align-items: center;
    justify-content: center;
    gap: 40px;
  }
  .card {
    position: relative;
    width: 520px;
    height: 297px;
    background: var(--card);
    overflow: hidden;
  }

  /* Founder side */
  .card-front .brand-mark {
    position: absolute;
    right: 36px;
    top: 0;
    width: 150px;
    height: 150px;
    margin-top: 20px;
    background: var(--rose);
  }
  .contact-block {
    position: absolute;
    left: 30px;
    bottom: 24px;
    color: var(--white);
  }
  .person-name {
    color: var(--rose);
    font-weight: 600;
    font-size: 18px;
    line-height: 1.15;
  }
  .person-title {
    font-size: 12px;
    line-height: 1.2;
    margin-bottom: 12px;
  }
  .abn {
    font-size: 15px;
    margin-bottom: 10px;
  }
  .abn-label {
    color: var(--rose);
    font-weight: 600;
  }
  .contact-list {
    list-style: none;
    font-size: 13.5px;
  }
  .contact-list li {
    display: flex;
    align-items: center;
    gap: 10px;
    line-height: 22px;
  }
  .contact-icon {
    width: 12px;
    height: 12px;
    flex: none;
  }
  .dot-icon {
    width: 11px;
    height: 11px;
    border-radius: 50%;
    background: var(--rose);
    flex: none;
  }

  /* Brand side */
  .card-back {
    display: flex;
    flex-direction: column;
    align-items: center;
    justify-content: center;
    gap: 26px;
  }
  .card-back .brand-mark {
    width: 70px;
    height: 70px;
    background: var(--rose);
  }
  .wordmark {
    color: var(--rose);
    font-weight: 400;
    font-size: 40px;
    letter-spacing: 14px;
    padding-left: 14px;
  }
</style>
</head>
<body>
<main class="canvas">

  <section class="card card-front" aria-label="Founder card">
    <div class="brand-mark" aria-hidden="true"></div>
    <div class="contact-block">
      <p class="person-name">Sunela Parvaniya</p>
      <p class="person-title">Founder</p>
      <p class="abn"><span class="abn-label">ABN:</span> 58219740312</p>
      <ul class="contact-list">
        <li>
          <svg class="contact-icon" viewBox="0 0 24 24" aria-hidden="true"><path fill="#e39a92" d="M6.6 10.8a15.1 15.1 0 0 0 6.6 6.6l2.2-2.2c.3-.3.7-.4 1-.2 1.1.4 2.3.6 3.6.6.6 0 1 .4 1 1V20c0 .6-.4 1-1 1A17 17 0 0 1 3 4c0-.6.4-1 1-1h3.5c.6 0 1 .4 1 1 0 1.3.2 2.5.6 3.6.1.3 0 .7-.2 1z"/></svg>
          +61452913307
        </li>
        <li>
          <svg class="contact-icon" viewBox="0 0 24 24" aria-hidden="true"><path fill="#e39a92" d="M2 5h20v14H2z"/><path fill="none" stroke="#1f1f1f" stroke-width="2" d="M2 5l10 8 10-8"/></svg>
          sunela@quiremo.com.au
        </li>
        <li><span class="dot-icon" aria-hidden="true"></span>www.quiremo.com.au</li>
        <li><span class="dot-icon" aria-hidden="true"></span>quiremo_jewellery</li>
        <li><span class="dot-icon" aria-hidden="true"></span>@quiremojewellery</li>
      </ul>
    </div>
  </section>

  <section class="card card-back" aria-label="Brand card">
    <div class="brand-mark" aria-hidden="true"></div>
    <p class="wordmark">QUIREMO</p>
  </section>

</main>
</body>
</html>
```